Business Card Design for ReaL ESTATE AGENT

New Business Cards for a real estate agent in Jacksonville, FL. My specialty is urban core, historic districts but sell through out the city. Company Name is Ninth and Crest Realty a division of the Dunholt Companies. The card needs to convey an essence of professionalism, knowledge and success.

Target Market(s)

Home buyers and Sellers

Industry/Entity Type

Real Estate

Contact Information for Business Card

Double sided

Font styles to use
Sans Serif

Requirements
Must have
• My logs and photo (provided). My contact information as follows:
• Owen Talbrick
• Cell 904-555-0183
• Office 904-555-0147
• Email owentalbrick@mailbrook.example
Nice to have
• Tag Line - Exceptional Effort. Proven Results.

```html
<!DOCTYPE html>
<html lang="en">
<head>
<meta charset="utf-8">
<title>Ninth and Crest Realty – Business Card</title>
<link rel="stylesheet" href="https://fonts.googleapis.com/css2?family=Source+Sans+3:wght@400;600;700&display=swap">
<style>
  :root {
    --stage: #000000;
    --card: #ffffff;
    --brand-green: #1d5a3b;
    --brand-orange: #e6553a;
    --photo-light: #e9e4df;
    --photo-dark: #3b3c40;
  }
  html, body {
    margin: 0;
    padding: 0;
    width: 1200px;
    height: 900px;
    overflow: hidden;
    background: var(--stage);
    font-family: "Source Sans 3", "Helvetica Neue", Arial, sans-serif;
  }
  .canvas {
    position: relative;
    width: 1200px;
    height: 900px;
  }
  .card {
    position: absolute;
    background: var(--card);
    overflow: hidden;
  }
  .card--front {
    left: 120px;
    top: 275px;
    width: 477px;
    height: 293px;
    border-radius: 0 48px 0 48px;
  }
  .card--back {
    left: 607px;
    top: 273px;
    width: 476px;
    height: 293px;
    border-radius: 48px 0 48px 0;
  }
  .portrait {
    position: absolute;
    left: 0;
    top: 2px;
    width: 226px;
    height: 291px;
    background: linear-gradient(180deg, var(--photo-light) 0%, #cdbfb4 45%, var(--photo-dark) 100%);
  }
  .identity {
    position: absolute;
    right: 32px;
    top: 150px;
    text-align: right;
  }
  .identity__name {
    margin: 0;
    font-size: 19px;
    font-weight: 700;
    color: var(--brand-green);
    line-height: 1.1;
  }
  .identity__title {
    margin: 3px 0 0;
    font-size: 13px;
    font-weight: 400;
    color: var(--brand-orange);
  }
  .contact {
    position: absolute;
    right: 30px;
    top: 210px;
    margin: 0;
    padding: 0;
    list-style: none;
  }
  .contact__item {
    display: flex;
    justify-content: flex-end;
    align-items: center;
    gap: 6px;
    height: 19px;
    font-size: 13px;
    color: var(--brand-orange);
    white-space: nowrap;
  }
  .contact__icon {
    width: 13px;
    height: 13px;
    display: block;
    flex: none;
  }
  .brand {
    position: absolute;
    left: 0;
    right: 0;
    top: 112px;
    display: flex;
    justify-content: center;
    align-items: center;
    gap: 12px;
  }
  .brand__mark {
    width: 22px;
    height: 22px;
    background: var(--brand-green);
  }
  .brand__name {
    font-size: 30px;
    font-weight: 700;
    color: var(--brand-green);
    letter-spacing: 0.5px;
  }
  .tagline {
    position: absolute;
    left: 0;
    right: 0;
    top: 162px;
    margin: 0;
    text-align: center;
    font-size: 14px;
    font-weight: 600;
    color: var(--brand-orange);
    letter-spacing: 0.3px;
  }
</style>
</head>
<body>
<main class="canvas">
  <section class="card card--front">
    <div class="portrait" role="img" aria-label="Portrait photo of the agent in a dark suit and red tie"></div>
    <div class="identity">
      <p class="identity__name">Owen Talbrick</p>
      <p class="identity__title">Managing Director</p>
    </div>
    <ul class="contact">
      <li class="contact__item">
        <span>Cell 904-555-0183</span>
        <svg class="contact__icon" viewBox="0 0 13 13" aria-hidden="true">
          <rect width="13" height="13" fill="var(--brand-green)"/>
          <path d="M3 5.2c0-1 1.6-1.6 3.5-1.6S10 4.2 10 5.2v.6H8.4v-.8H4.6v.8H3z" fill="#fff"/>
          <rect x="3.6" y="6.4" width="5.8" height="3.4" fill="#fff"/>
        </svg>
      </li>
      <li class="contact__item">
        <span>Office 904-555-0147</span>
        <svg class="contact__icon" viewBox="0 0 13 13" aria-hidden="true">
          <rect width="13" height="13" fill="var(--brand-green)"/>
          <path d="M3 5.2c0-1 1.6-1.6 3.5-1.6S10 4.2 10 5.2v.6H8.4v-.8H4.6v.8H3z" fill="#fff"/>
          <rect x="3.6" y="6.4" width="5.8" height="3.4" fill="#fff"/>
        </svg>
      </li>
      <li class="contact__item">
        <span>owentalbrick@mailbrook.example</span>
        <svg class="contact__icon" viewBox="0 0 13 13" aria-hidden="true">
          <rect width="13" height="13" fill="var(--brand-green)"/>
          <rect x="2.8" y="4" width="7.4" height="5" fill="#fff"/>
          <path d="M2.8 4l3.7 2.8L10.2 4" fill="none" stroke="var(--brand-green)" stroke-width="0.8"/>
        </svg>
      </li>
    </ul>
  </section>

  <section class="card card--back">
    <div class="brand">
      <span class="brand__mark"></span>
      <span class="brand__name">Ninth and Crest Realty</span>
    </div>
    <p class="tagline">Exceptional Effort. Proven Results.</p>
  </section>
</main>
</body>
</html>
```